Business Card Design For A Renovation Contractor Company

We need a business card for a new company based in Singapore, our company name is "RB Tolvane". We are a renovation contractor that builds designs into reality. We build more of F&B restaurants, retail stores and commercial offices. We work very closely with designers. The final design should communicate to our client that we are a company that you can trust, that will plan and complete your project without giving you a headache. I like my client to remember my company as "RB". The beauty of SIMPLE is important.

Industry/Entity Type

Contractor

Requirements
Nice to have
• Black or Red base

```html
<!DOCTYPE html>
<html lang="en">
<head>
<meta charset="utf-8">
<title>RB Tolvane – Business Card</title>
<link href="https://fonts.googleapis.com/css2?family=Arimo:wght@400;700&display=swap" rel="stylesheet">
<style>
  :root {
    --brand-red: #ec2227;
    --ink-black: #1c1c1c;
    --card-white: #ffffff;
    --backdrop: #e4e4ea;
    --card-w: 760px;
    --card-h: 434px;
  }
  * { box-sizing: border-box; margin: 0; padding: 0; }
  html, body {
    width: 1200px;
    height: 987px;
    overflow: hidden;
    background: var(--backdrop);
    font-family: "Arimo", Arial, sans-serif;
  }
  .card-sheet {
    width: 1200px;
    height: 987px;
    display: flex;
    flex-direction: column;
    align-items: center;
    justify-content: center;
    gap: 50px;
  }
  .card {
    position: relative;
    width: var(--card-w);
    height: var(--card-h);
    border-radius: 24px;
    overflow: hidden;
    box-shadow: 0 6px 18px rgba(0,0,0,0.12);
  }

  /* Front */
  .card-front { background: var(--card-white); }
  .card-front .sweep { position: absolute; inset: 0; }
  .brand-block {
    position: absolute;
    left: 330px;
    top: 78px;
    width: 380px;
  }
  .brand-name {
    display: flex;
    align-items: center;
    gap: 14px;
    font-size: 62px;
    font-weight: 400;
    color: var(--brand-red);
    line-height: 1;
    letter-spacing: -1px;
    white-space: nowrap;
  }
  .brand-dot {
    width: 22px; height: 22px;
    border-radius: 50%;
    background: var(--ink-black);
    flex: none;
  }
  .brand-tagline {
    margin-top: 6px;
    padding-top: 4px;
    border-top: 2px solid var(--ink-black);
    font-size: 20px;
    color: var(--ink-black);
    letter-spacing: 0.5px;
    white-space: nowrap;
  }
  .contact {
    position: absolute;
    top: 300px;
    color: var(--card-white);
    font-size: 19px;
    line-height: 1.3;
    white-space: nowrap;
  }
  .contact-person {
    right: calc(var(--card-w) - 300px);
    text-align: right;
  }
  .contact-person .person-name { font-size: 28px; font-weight: 700; }
  .contact-person .person-title { font-size: 20px; margin-bottom: 4px; }
  .contact-divider {
    position: absolute;
    left: 320px;
    top: 296px;
    width: 1.5px;
    height: 120px;
    background: rgba(255,255,255,0.7);
  }
  .contact-lines { left: 342px; top: 306px; font-size: 21px; line-height: 1.28; }

  /* Back */
  .card-back {
    background: var(--brand-red);
    display: flex;
    flex-direction: column;
    align-items: center;
    justify-content: center;
    gap: 36px;
  }
  .back-brand {
    display: flex;
    align-items: center;
    gap: 22px;
    color: var(--card-white);
    font-size: 92px;
    font-weight: 400;
    letter-spacing: -1px;
  }
  .back-brand .brand-dot {
    width: 40px; height: 40px;
    background: var(--card-white);
  }
  .back-web {
    color: var(--card-white);
    font-size: 24px;
    letter-spacing: 6px;
  }
</style>
</head>
<body>
<main class="card-sheet">

  <section class="card card-front" aria-label="Business card front">
    <svg class="sweep" width="760" height="434" viewBox="0 0 760 434" aria-hidden="true">
      <path fill="var(--ink-black)" d="M0,30 C180,200 430,248 760,262 L760,268 C420,262 180,215 0,62 Z"/>
      <path fill="var(--brand-red)" d="M0,78 C180,235 420,268 760,276 L760,434 L0,434 Z"/>
    </svg>

    <div class="brand-block">
      <div class="brand-name"><span class="brand-dot"></span>RB Tolvane</div>
      <div class="brand-tagline">turning designs into spaces</div>
    </div>

    <div class="contact contact-person">
      <div class="person-name">Your Name</div>
      <div class="person-title">Title</div>
      <div>Door No. Street Name</div>
      <div>City Name, State, Zip Code</div>
    </div>
    <div class="contact-divider"></div>
    <div class="contact contact-lines">
      <div>p: 123-456-7890</div>
      <div>c: 123-456-7890</div>
      <div>e: info@rbtolvane.com</div>
      <div>w: www.rbtolvane.com</div>
    </div>
  </section>

  <section class="card card-back" aria-label="Business card back">
    <div class="back-brand"><span class="brand-dot"></span>RB Tolvane</div>
    <div class="back-web">www.rbtolvane.com</div>
  </section>

</main>
</body>
</html>
```